****Business Card Design for Quarrystone Development. Design based around attached logo/company name

I’m looking for business card design for my company Quarrystone Development Group,LLC. Design should be professional, sharp and minimal. Outside of the attached logos, greyscale colors for remainder of cards. My thoughts are two-sided card with attached logo on one side and my info on the other but open to one-sided as well with right design.
Target Market(s)
Real estate professionals including banks, private investors, property owners, developers, commercial tenants like Brewlantern, Grovika or Tanquist’s.
Industry/Entity Type
Commercial real estate development and investments.
Contact Information for Business Card
Name, title, email, phone #’s, web address and physical address
Font styles to use
Other font styles liked:
- Helvetica, Garamond, etc
Colors
Designer to choose only greyscale colors for use in the design.
Requirements
Must have
- Attached logo first or second options.
Nice to have
- Two sided card with logo on one side. Attached Logo/company name can be laid out any way that flows as long as it’s legible.name
Should not have
- No loud colors. ***Please do not include logo, I have removed the company design with a logo image.

```html
<!DOCTYPE html>
<html lang="en">
<head>
<meta charset="utf-8">
<title>Quarrystone Development Group, LLC — Business Card</title>
<link rel="stylesheet" href="https://fonts.googleapis.com/css2?family=Cormorant+Garamond:wght@500&family=Arimo:wght@400&display=swap">
<style>
  :root {
    --backdrop: #dcdcdc;
    --card-light: #ffffff;
    --card-dark-top: #5b5f6b;
    --card-dark-bottom: #2b2e38;
    --ink: #5f636e;
    --ink-soft: #777b85;
    --rule: #8a8d96;
    --ink-reverse: #ffffff;
  }
  * { margin: 0; padding: 0; box-sizing: border-box; }
  html, body {
    width: 1200px;
    height: 1200px;
    overflow: hidden;
    background: var(--backdrop);
  }
  .stage {
    position: relative;
    width: 1200px;
    height: 1200px;
  }
  .card {
    position: absolute;
    left: 257px;
    width: 686px;
    height: 391px;
    box-shadow: 0 10px 22px rgba(0,0,0,0.18);
  }
  .card--front { top: 165px; background: var(--card-light); }
  .card--back {
    top: 626px;
    background: linear-gradient(200deg, var(--card-dark-top) 0%, var(--card-dark-bottom) 65%);
  }

  .wordmark {
    position: absolute;
    font-family: "Cormorant Garamond", Georgia, serif;
    font-weight: 500;
    color: var(--ink);
    text-transform: uppercase;
    line-height: 1;
    text-align: right;
  }
  .wordmark__name { display: block; letter-spacing: 0.02em; }
  .wordmark__group { display: block; letter-spacing: 0.04em; }

  .card--front .wordmark { left: 68px; top: 178px; width: 300px; }
  .card--front .wordmark__name { font-size: 38px; }
  .card--front .wordmark__group { font-size: 15.5px; margin-top: 6px; }

  .card--back .wordmark {
    left: 0; right: 0; top: 150px;
    text-align: center;
    color: var(--ink-reverse);
  }
  .card--back .wordmark__name { font-size: 62px; }
  .card--back .wordmark__group { font-size: 25px; margin-top: 10px; }

  .divider {
    position: absolute;
    left: 379px;
    top: 100px;
    width: 1px;
    height: 202px;
    background: var(--rule);
    opacity: 0.7;
  }

  .contact {
    position: absolute;
    left: 400px;
    top: 96px;
    font-family: Arimo, Helvetica, Arial, sans-serif;
    color: var(--ink-soft);
  }
  .contact__name {
    font-family: "Cormorant Garamond", Georgia, serif;
    font-weight: 500;
    font-size: 23px;
    letter-spacing: 0.03em;
    text-transform: uppercase;
    color: var(--ink);
    line-height: 1;
  }
  .contact__title { font-size: 14.5px; margin-top: 5px; color: var(--ink); }
  .contact__address { font-size: 14.5px; line-height: 19px; margin-top: 14px; }
  .contact__list { list-style: none; margin-top: 15px; font-size: 14.5px; }
  .contact__list li {
    display: flex;
    align-items: center;
    height: 19.5px;
  }
  .contact__icon {
    width: 11px;
    height: 11px;
    margin-right: 13px;
    fill: var(--ink);
  }
</style>
</head>
<body>
<main class="stage">

  <section class="card card--front" aria-label="Business card front">
    <div class="wordmark">
      <span class="wordmark__name">Quarrystone</span>
      <span class="wordmark__group">Development Group, LLC</span>
    </div>

    <div class="divider"></div>

    <div class="contact">
      <p class="contact__name">Daniel Reyes</p>
      <p class="contact__title">President</p>
      <p class="contact__address">4210 Alder Ridge Road<br>Anchorage, Alaska 99508</p>
      <ul class="contact__list">
        <li>
          <svg class="contact__icon" viewBox="0 0 12 12" aria-hidden="true"><path d="M2.4 0.6l2 2.2-1 1.4c.7 1.5 1.9 2.7 3.4 3.4l1.4-1 2.2 2-1.2 2.2C4.8 11 1 7.2.2 1.8z"/></svg>
          369-555-0142
        </li>
        <li>
          <svg class="contact__icon" viewBox="0 0 12 12" aria-hidden="true"><rect x="3" y="0.5" width="6" height="3"/><rect x="0.5" y="4" width="11" height="5" rx="1"/><rect x="3" y="8" width="6" height="3.5"/></svg>
          369-555-0187
        </li>
        <li>
          <svg class="contact__icon" viewBox="0 0 12 12" aria-hidden="true"><path d="M0.5 2.5h11v7h-11z M1 3l5 4 5-4" fill="none" stroke="#5f636e" stroke-width="1.2"/></svg>
          name@quarrystone.com
        </li>
        <li>
          <svg class="contact__icon" viewBox="0 0 12 12" aria-hidden="true"><circle cx="6" cy="6" r="5.5"/><path d="M4 3.5c1 .5 1.5 1.5 1 2.5l-1.5.5M7.5 7.5l1.5 1.5" stroke="#ffffff" stroke-width="1" fill="none"/></svg>
          www.quarrystone.com
        </li>
      </ul>
    </div>
  </section>

  <section class="card card--back" aria-label="Business card back">
    <div class="wordmark">
      <span class="wordmark__name">Quarrystone</span>
      <span class="wordmark__group">Development Group, LLC</span>
    </div>
  </section>

</main>
</body>
</html>
```